BrivoTerna. Lantern of the Steady Harvest. Business card

Professional business card for BrivoTerna (Lantern of the Steady Harvest)
My rationale: Strategy-> Execution-> Results-> Value that lead to the BrivoTerna name: We put the Lantern of the Steady Harvest.
We deliver value to our customers helping them at defining a good strategy (cyan arrow). 90% of well formulated strategies fail due to poor execution so we also consider strategical execution very important (green arrow). Due to the execution we obtain the results (blue arrow). Finally, the results provide feedback to redefine strategy, and the new strategy has to be executed and new results obtained providing new feedback and on and on. It's like a wheel that finally, must create corporate value: value for shareholders, staholders, employees, providers...-

Target Market(s)

CEOs and steering comitees , invewrnent funds

Industry/Entity Type

Business Consultant

Contact Information for Business Card

Teodoro Vinsquel
CEO & Founder
teodoro.vinsquel@brivoterna-example.com
Mobile: +34 655.803.912
www.brivoterna-example.com

Colors

Designer to choose colors to be used in the design.

Requirements
Nice to have
• Nice to hace the words: Strategy, execution, results
• Nice to vave the claim: Lantern of the Steady Harvest
• The three colors should be shown:
• cyan for STRATEGY
• green for EXECUTION
• blue for RESULTS
Should not have
• Complete black background

```html
<!DOCTYPE html>
<html lang="en">
<head>
<meta charset="utf-8">
<title>BrivoTerna — Business Card</title>
<link href="https://fonts.googleapis.com/css2?family=Roboto:wght@400;500;700&display=swap" rel="stylesheet">
<style>
  :root {
    --page-bg: #ececec;
    --brand-blue: #023093;
    --brand-cyan: #1ba3e8;
    --card-white: #ffffff;
    --text-blue: #1a3b8f;
    --faint-blue: #c4cde3;
    --card-shadow: rgba(0, 0, 0, 0.28);
  }
  * { margin: 0; padding: 0; box-sizing: border-box; }
  html, body {
    width: 1200px;
    height: 954px;
    overflow: hidden;
    background: var(--page-bg);
    font-family: "Roboto", Arial, sans-serif;
  }
  .canvas {
    position: relative;
    width: 1200px;
    height: 954px;
  }
  .card {
    position: absolute;
    top: 344px;
    width: 525px;
    height: 300px;
    overflow: hidden;
    box-shadow: 0 3px 6px var(--card-shadow);
  }
  .card-front {
    left: 68px;
    background: var(--brand-blue);
  }
  .card-back {
    left: 606px;
    background: var(--card-white);
  }
  .front-wordmark {
    position: absolute;
    left: 36px;
    top: 158px;
    font-size: 40px;
    font-weight: 700;
    letter-spacing: -0.5px;
    color: var(--card-white);
  }
  .front-decoration {
    position: absolute;
    left: 376px;
    top: 140px;
    width: 126px;
    height: 156px;
    background: linear-gradient(90deg, rgba(255,255,255,0.18), rgba(255,255,255,0));
  }
  .back-decoration {
    position: absolute;
    left: 0;
    top: 0;
    width: 150px;
    height: 300px;
    background: linear-gradient(90deg, rgba(255,255,255,1) 0%, var(--faint-blue) 100%);
    opacity: 0.75;
  }
  .back-wordmark {
    position: absolute;
    left: 226px;
    top: 62px;
    font-size: 38px;
    font-weight: 700;
    letter-spacing: -0.5px;
    color: var(--brand-blue);
  }
  .person-name {
    position: absolute;
    left: 226px;
    top: 157px;
    font-size: 16px;
    font-weight: 500;
    color: var(--brand-cyan);
  }
  .person-title {
    position: absolute;
    left: 226px;
    top: 176px;
    font-size: 12px;
    color: var(--text-blue);
  }
  .contact-list {
    position: absolute;
    left: 226px;
    top: 204px;
    list-style: none;
  }
  .contact-item {
    display: flex;
    align-items: center;
    height: 20px;
    font-size: 12.5px;
    color: var(--text-blue);
  }
  .contact-icon {
    width: 10px;
    height: 10px;
    margin-right: 5px;
    fill: var(--brand-cyan);
    flex: none;
  }
</style>
</head>
<body>
<main class="canvas">
  <section class="card card-front" aria-label="Card front">
    <div class="front-decoration" role="img" aria-label="Faint brand arrow decoration"></div>
    <h1 class="front-wordmark">BrivoTerna</h1>
  </section>

  <section class="card card-back" aria-label="Card back">
    <div class="back-decoration" role="img" aria-label="Large faint brand arrow decoration"></div>
    <h2 class="back-wordmark">BrivoTerna</h2>
    <p class="person-name">Teodoro Vinsquel</p>
    <p class="person-title">CEO &amp; Founder</p>
    <ul class="contact-list">
      <li class="contact-item">
        <svg class="contact-icon" viewBox="0 0 10 10" aria-hidden="true"><path d="M2 0.5 L3.6 2.6 L2.8 3.6 Q3.8 5.9 6.4 7.2 L7.4 6.4 L9.5 8 L8.4 9.5 Q4.5 9.3 2 6.5 Q0.3 4.2 0.5 1.6 Z"/></svg>
        +34 655.803.912
      </li>
      <li class="contact-item">
        <svg class="contact-icon" viewBox="0 0 10 10" aria-hidden="true"><circle cx="5" cy="5" r="4.6"/><path d="M0.8 5 H9.2 M5 0.5 V9.5" stroke="#fff" stroke-width="0.8"/></svg>
        www.brivoterna-example.com
      </li>
      <li class="contact-item">
        <svg class="contact-icon" viewBox="0 0 10 10" aria-hidden="true"><rect x="0.3" y="2" width="9.4" height="6.4"/><path d="M0.5 2.3 L5 5.6 L9.5 2.3" fill="none" stroke="#fff" stroke-width="0.8"/></svg>
        teodoro.vinsquel@brivoterna-example.com
      </li>
    </ul>
  </section>
</main>
</body>
</html>
```